MV Decor

There is a sample provided with the arabic text of the business card. please copy paste the same text and the same Logo (The two triangles) Just try to incorproate the Brown background attached (you are free to change the colors) Id like the colors to be mainly shades of black and red.

```html
<!DOCTYPE html>
<html lang="ar">
<head>
<meta charset="utf-8">
<title>MV Decor – Business Card</title>
<link rel="stylesheet" href="https://fonts.googleapis.com/css2?family=Aref+Ruqaa:wght@400;700&family=Tajawal:wght@400;700&display=swap">
<style>
  :root {
    --page: #ecebe8;
    --red: #c91f40;
    --red-light: #d83a57;
    --red-deep: #b3173a;
    --charcoal: #262826;
    --white: #ffffff;
    --dot: #2a2a2a;
  }
  * { margin: 0; padding: 0; box-sizing: border-box; }
  html, body {
    width: 1125px; height: 1200px; overflow: hidden;
    background: var(--page);
    font-family: "Tajawal", sans-serif;
  }
  .card {
    position: absolute; left: 162px;
    width: 800px; height: 457px;
    overflow: hidden;
    box-shadow: 0 3px 10px rgba(0,0,0,.25);
    background: var(--red);
  }
  .card--front { top: 113px; }
  .card--back { top: 630px; }
  .texture {
    position: absolute; inset: 0;
    background:
      radial-gradient(ellipse at 45% 35%, var(--red-light) 0%, transparent 60%),
      linear-gradient(160deg, var(--red) 0%, var(--red-deep) 100%);
  }
  .panel { position: absolute; inset: 0; }
  .brand {
    position: absolute;
    display: flex; align-items: center; gap: 12px;
    color: var(--white);
    font-weight: 700;
    letter-spacing: 2px;
    white-space: nowrap;
  }
  .brand__mark { width: 14px; height: 14px; background: var(--charcoal); }
  .card--front .brand { left: 100px; top: 196px; font-size: 44px; }
  .card--back .brand { left: 100px; top: 200px; font-size: 42px; }
  .contact {
    position: absolute; right: 46px; top: 50px;
    direction: rtl; text-align: right; color: var(--white);
  }
  .contact__name {
    font-family: "Aref Ruqaa", serif; font-weight: 700;
    font-size: 27px; line-height: 1.2;
  }
  .contact__role {
    font-family: "Aref Ruqaa", serif; font-size: 17px;
    padding-right: 62px; margin-top: -2px;
  }
  .contact__phone {
    position: absolute; right: 46px; top: 150px;
    direction: ltr; display: flex; align-items: center; gap: 6px;
    color: var(--white); font-size: 21px; font-weight: 700;
  }
  .quals {
    position: absolute; right: 46px; top: 298px;
    direction: rtl; text-align: right; list-style: none;
    color: var(--white); font-size: 19px; line-height: 26px;
  }
  .quals--bulleted {
    right: 110px; top: 100px;
    font-size: 23px; line-height: 32px;
  }
  .quals--bulleted li { display: block; white-space: nowrap; }
  .quals--bulleted li::after {
    content: ""; display: inline-block;
    width: 8px; height: 8px; border-radius: 50%;
    background: var(--dot);
    margin-right: 10px; vertical-align: middle;
  }
</style>
</head>
<body>

<section class="card card--front">
  <div class="texture" role="img" aria-label="Red background with a soft square-tile pattern"></div>
  <svg class="panel" width="800" height="457" viewBox="0 0 800 457">
    <polygon points="296,0 800,0 800,457 296,457 462,228" fill="#ffffff"/>
    <polygon points="308,0 800,0 800,457 308,457 474,228" fill="var(--charcoal)"/>
  </svg>
  <div class="brand"><span class="brand__mark"></span>MV DECOR</div>
  <div class="contact">
    <p class="contact__name">المهندس / خالد سالم الراشد</p>
    <p class="contact__role">أستاذ جامعي</p>
  </div>
  <p class="contact__phone">
    <svg width="17" height="17" viewBox="0 0 24 24"><path fill="#fff" d="M6.6 10.8a15.1 15.1 0 0 0 6.6 6.6l2.2-2.2c.3-.3.7-.4 1-.2 1.1.4 2.3.6 3.6.6.6 0 1 .4 1 1V20c0 .6-.4 1-1 1C10.6 21 3 13.4 3 4c0-.6.4-1 1-1h3.5c.6 0 1 .4 1 1 0 1.3.2 2.5.6 3.6.1.3 0 .7-.2 1z"/></svg>
    39004512 / 66021378
  </p>
  <ul class="quals">
    <li>ماجستير هندسة ديكور</li>
    <li>دبلوم عالي فن تشكيلي</li>
    <li>جامعة الفنون الجميلة (ليون)</li>
    <li>استشارات هندسية - فنية</li>
  </ul>
</section>

<section class="card card--back">
  <div class="texture" role="img" aria-label="Red background with a soft square-tile pattern"></div>
  <div class="brand"><span class="brand__mark"></span>MV DECOR</div>
  <ul class="quals quals--bulleted">
    <li>ماجستير هندسة ديكور</li>
    <li>دبلوم عالي فن تشكيلي</li>
    <li>جامعة الفنون الجميلة (ليون)</li>
    <li>استشارات هندسية - فنية</li>
    <li>ماجستير هندسة ديكور</li>
    <li>دبلوم عالي فن تشكيلي</li>
    <li>جامعة الفنون الجميلة (ليون)</li>
    <li>استشارات هندسية - فنية</li>
  </ul>
</section>

</body>
</html>
```